Automotive Accessories Business Card

Design a business template that match our new logo design and our industry.

https://www.qelmotorgear.com/

Target Market(s)

Aftermarket auto parts and accessories

Industry/Entity Type

automotive

Contact Information for Business Card

company logo

Font styles to use
Serif
Sans Serif

Colors
EB3D1F
EC4F4E
F09395
F8D3D4
FCEDEE

```html
<!DOCTYPE html>
<html lang="en">
<head>
<meta charset="UTF-8">
<title>QEL Motor Gear – Business Card</title>
<link rel="stylesheet" href="https://fonts.googleapis.com/css2?family=Arimo:wght@400;700&display=swap">
<style>
  :root {
    --page-bg: #2a2a2a;
    --card-bg: #0c0c0c;
    --brand-red: #dc2128;
    --text-white: #ffffff;
    --divider: #5a5a5a;
  }
  * { box-sizing: border-box; margin: 0; padding: 0; }
  html, body {
    width: 1200px;
    height: 900px;
    overflow: hidden;
    background: var(--page-bg);
    font-family: "Arimo", Arial, sans-serif;
    color: var(--text-white);
  }
  .canvas {
    position: relative;
    width: 1200px;
    height: 900px;
  }
  .card {
    position: absolute;
    left: 250px;
    width: 700px;
    height: 400px;
    background: var(--card-bg);
  }
  .card--back { top: 40px; }
  .card--front { top: 460px; }

  /* Brand name lockup */
  .brand {
    display: flex;
    align-items: center;
    gap: 14px;
    font-weight: 700;
    color: var(--text-white);
    text-transform: uppercase;
    letter-spacing: 1px;
    white-space: nowrap;
  }
  .brand__mark {
    background: var(--brand-red);
    flex: none;
  }
  .card--back .brand {
    position: absolute;
    left: 50%;
    top: 50%;
    transform: translate(-50%, -50%);
    font-size: 44px;
  }
  .card--back .brand__mark { width: 38px; height: 38px; }

  .card--front .brand {
    position: absolute;
    left: 48px;
    top: 205px;
    font-size: 26px;
  }
  .card--front .brand__mark { width: 24px; height: 24px; }

  .divider {
    position: absolute;
    left: 355px;
    top: 70px;
    width: 1px;
    height: 260px;
    background: var(--divider);
  }

  .contact {
    position: absolute;
    left: 385px;
    top: 82px;
    width: 300px;
  }
  .contact__name {
    color: var(--brand-red);
    font-weight: 700;
    font-size: 24px;
    text-transform: uppercase;
    letter-spacing: 0.5px;
    line-height: 1.05;
  }
  .contact__role {
    font-size: 17px;
    margin-bottom: 22px;
  }
  .contact__list { list-style: none; }
  .contact__item {
    display: flex;
    align-items: center;
    gap: 10px;
    font-size: 16px;
    line-height: 1.7;
  }
  .contact__icon { width: 16px; height: 16px; flex: none; }
  .contact__highlight { color: var(--brand-red); }
  .contact__address {
    margin-top: 18px;
    font-size: 16px;
    line-height: 1.35;
  }
</style>
</head>
<body>
<main class="canvas">

  <section class="card card--back" aria-label="Business card back">
    <div class="brand">
      <span class="brand__mark"></span>
      <span class="brand__name">QEL Motor Gear</span>
    </div>
  </section>

  <section class="card card--front" aria-label="Business card front">
    <div class="brand">
      <span class="brand__mark"></span>
      <span class="brand__name">QEL Motor Gear</span>
    </div>

    <div class="divider"></div>

    <div class="contact">
      <p class="contact__name">Daniel Reyes</p>
      <p class="contact__role">Managing Director</p>
      <ul class="contact__list">
        <li class="contact__item">
          <svg class="contact__icon" viewBox="0 0 16 16" aria-hidden="true">
            <path fill="var(--brand-red)" d="M3.6 1.5l2.3 2.6-1.3 1.6c.8 1.8 2.1 3.1 3.8 3.9l1.6-1.3 2.6 2.3-1.2 2.2C7 12.5 3 8.6 1.5 2.8z"/>
          </svg>
          <span>044-987 654 321</span>
        </li>
        <li class="contact__item">
          <svg class="contact__icon" viewBox="0 0 16 16" aria-hidden="true">
            <rect x="1" y="3" width="14" height="10" fill="var(--brand-red)"/>
            <path d="M1 3l7 6 7-6" fill="none" stroke="var(--card-bg)" stroke-width="1.3"/>
          </svg>
          <span>info@qelmotorgear.com</span>
        </li>
        <li class="contact__item">
          <svg class="contact__icon" viewBox="0 0 16 16" aria-hidden="true">
            <g fill="none" stroke="var(--brand-red)" stroke-width="1.3">
              <circle cx="8" cy="8" r="6.5"/>
              <ellipse cx="8" cy="8" rx="2.8" ry="6.5"/>
              <path d="M1.5 8h13M2.5 4.7h11M2.5 11.3h11"/>
            </g>
          </svg>
          <span>www.<span class="contact__highlight">qelmotorgear</span>.com</span>
        </li>
      </ul>
      <p class="contact__address">421, Address line goes here<br>45452, Country Name</p>
    </div>
  </section>

</main>
</body>
</html>
```